Business Card Design

Looking for business card designs for a new business. there will be two cards of the same design (both lots of information below in contact info). We would like the logo diagonally across the card with the information split above and below the logo similar to sketch. happy to look at similar alternatives
Please use same colours as in logo design

Industry/Entity Type

Business

Contact Information for Business Card

Dwight Halloran
mob - 0491 738 204
ph - 02 6148 3920
fax - 02 6148 3975
email - dwight@kestrelbeams.com.au
14 Larkmoor Road, Taminda NSW 2340

Colin Marchetti
mob - 0438 912 557
ph - 02 6148 3920
fax - 02 6148 3975
email - colin@kestrelbeams.com.au

```html
<!DOCTYPE html>
<html lang="en">
<head>
<meta charset="utf-8">
<title>Kestrel Beams — Business Card</title>
<link rel="stylesheet" href="https://fonts.googleapis.com/css2?family=Source+Sans+3:wght@400;600;700&display=swap">
<style>
  :root {
    --teal: #1b7c79;
    --ink: #0b0b0b;
    --paper: #ffffff;
    --backdrop: #e9e7e3;
    --text: #1c1c1c;
  }
  * { margin: 0; padding: 0; box-sizing: border-box; }
  html, body {
    width: 1146px; height: 1200px; overflow: hidden;
    background: var(--backdrop);
    font-family: "Source Sans 3", "Myriad Pro", Arial, sans-serif;
  }
  .canvas { position: relative; width: 1146px; height: 1200px; }

  .card { position: absolute; overflow: hidden; }
  .card--front {
    left: 179px; top: 47px; width: 941px; height: 541px;
    background: var(--paper);
    box-shadow: 0 2px 6px rgba(0,0,0,.18);
  }
  .card--back {
    left: 27px; top: 618px; width: 945px; height: 538px;
    background: var(--ink);
    box-shadow: 0 2px 6px rgba(0,0,0,.25);
  }

  .accent-tab { position: absolute; left: 0; top: 70px; width: 17px; height: 82px; background: var(--ink); }
  .person-name {
    position: absolute; left: 31px; top: 94px;
    font-size: 29px; font-weight: 700; color: var(--teal); letter-spacing: .2px;
  }

  .brand {
    position: absolute; display: flex; align-items: center; gap: 14px;
    font-weight: 700; white-space: nowrap; line-height: 1;
  }
  .brand__mark { display: block; }
  .brand--front { right: 32px; top: 72px; font-size: 64px; color: var(--ink); }
  .brand--front .brand__mark { width: 40px; height: 40px; background: var(--teal); }
  .brand--back { left: 0; right: 0; justify-content: center; top: 208px; font-size: 98px; color: var(--teal); }
  .brand--back .brand__mark { width: 58px; height: 58px; background: var(--teal); }

  .contact-list {
    position: absolute; left: 31px; top: 278px; list-style: none;
    font-size: 23px; color: var(--text); line-height: 36px;
  }
  .contact-list li { display: flex; align-items: center; gap: 6px; }
  .contact-list svg { width: 20px; height: 20px; fill: var(--teal); flex: none; }
  .address { position: absolute; left: 31px; top: 444px; font-size: 23px; color: var(--text); }

  .band-teal { position: absolute; left: 0; top: 515px; width: 628px; height: 26px; background: var(--teal); }
  .band-black { position: absolute; left: 641px; top: 505px; width: 300px; height: 36px; background: var(--ink); }

  .website {
    position: absolute; left: 0; right: 0; top: 424px; text-align: center;
    font-size: 30px; color: #fff; letter-spacing: 2.5px;
  }
  .website strong { font-weight: 700; }
</style>
</head>
<body>
<main class="canvas">

  <section class="card card--front" aria-label="Business card front">
    <span class="accent-tab"></span>
    <h1 class="person-name">Colin Marchetti</h1>

    <div class="brand brand--front">
      <span class="brand__mark"></span>
      <span class="brand__name">Kestrel Beams</span>
    </div>

    <ul class="contact-list">
      <li>
        <svg viewBox="0 0 20 20" aria-hidden="true"><circle cx="10" cy="10" r="9" fill="none" stroke="#1b7c79" stroke-width="1.6"/><path d="M6.5 5.5l2 .2.8 2.4-1.2 1a6 6 0 0 0 2.8 2.8l1-1.2 2.4.8.2 2c-4.5.6-8.6-3.5-8-8z"/></svg>
        <span>02 6148 3920</span>
      </li>
      <li>
        <svg viewBox="0 0 20 20" aria-hidden="true"><rect x="5" y="1" width="10" height="18" rx="1.5"/><rect x="6.5" y="3.5" width="7" height="5" fill="#fff"/><rect x="6.5" y="10.5" width="7" height="6" fill="#fff" opacity=".6"/></svg>
        <span>0438 912 557</span>
      </li>
      <li>
        <svg viewBox="0 0 20 20" aria-hidden="true"><path d="M4 9l2-4.5h8L16 9h2v5h-2v2h-2.5v-2h-7v2H4v-2H2V9z"/><rect x="6.5" y="6" width="7" height="3" fill="#fff"/></svg>
        <span>02 6148 3975</span>
      </li>
      <li>
        <svg viewBox="0 0 20 20" aria-hidden="true"><path d="M2 8l8-5 8 5v9H2z"/><path d="M3.5 8.5L10 13l6.5-4.5" fill="none" stroke="#fff" stroke-width="1.4"/></svg>
        <span>colin@kestrelbeams.com.au</span>
      </li>
    </ul>

    <p class="address">14 Larkmoor Road, Brellin NSW 2361</p>

    <span class="band-teal"></span>
    <span class="band-black"></span>
  </section>

  <section class="card card--back" aria-label="Business card back">
    <div class="brand brand--back">
      <span class="brand__mark"></span>
      <span class="brand__name">Kestrel Beams</span>
    </div>
    <p class="website">www.<strong>kestrelbeams</strong>.com.au</p>
  </section>

</main>
</body>
</html>
```